Business Card for a Dental Office

The design should communicate integrity, quality and reliability. We also want the card look elegant, simple, but still stand out, different from the traditional-dental-office business card.

Industry/Entity Type

Business

```html
<!DOCTYPE html>
<html lang="en">
<head>
<meta charset="utf-8">
<title>Harbour Lane Dental – Business Card</title>
<link href="https://fonts.googleapis.com/css2?family=Oswald:wght@500&family=Open+Sans:wght@400;600;700&display=swap" rel="stylesheet">
<style>
  :root {
    --backdrop: #5b3f2c;
    --card-white: #ffffff;
    --card-black: #000000;
    --ink: #111111;
    --gold: #c9b21a;
    --gold-bright: #f2e426;
    --gold-deep: #a89414;
    --tagline-gold: #b8a21c;
  }
  * { margin: 0; padding: 0; box-sizing: border-box; }
  html, body {
    width: 1200px; height: 1000px; overflow: hidden;
    background: var(--backdrop);
  }
  .canvas { position: relative; width: 1200px; height: 1000px; }

  .card {
    position: absolute; left: 265px; width: 666px; height: 397px;
    overflow: hidden;
    box-shadow: 0 6px 14px rgba(0,0,0,.45);
  }
  .card--front { top: 73px; background: linear-gradient(160deg, #ffffff 55%, #f1f1f1); }
  .card--back  { top: 533px; background: var(--card-black); }

  .brand { position: absolute; display: flex; align-items: center; gap: 14px; }
  .brand__mark { width: 58px; height: 58px; background: var(--ink); flex: none; }
  .brand__text { display: flex; flex-direction: column; }
  .brand__name {
    font-family: "Oswald", sans-serif; font-weight: 500;
    font-size: 33px; line-height: 1; letter-spacing: .3px; color: var(--ink);
    text-transform: uppercase; white-space: nowrap;
  }
  .brand__tagline {
    font-family: "Open Sans", sans-serif; font-weight: 600;
    font-size: 13.5px; letter-spacing: 1.4px; color: var(--tagline-gold);
    text-transform: uppercase; margin-top: 4px; white-space: nowrap;
  }
  .card--front .brand { left: 33px; top: 80px; }
  .card--back .brand { left: 97px; top: 157px; }
  .card--back .brand__mark { width: 110px; height: 110px; background: var(--card-white); }
  .card--back .brand__name { color: var(--card-white); font-size: 36px; }
  .card--back .brand__tagline { font-size: 14.5px; }

  .holder { position: absolute; left: 33px; top: 203px; right: 32px; font-family: "Open Sans", sans-serif; color: var(--ink); }
  .holder__name { font-size: 19px; font-weight: 700; line-height: 1.2; }
  .holder__role { display: flex; align-items: center; gap: 10px; font-size: 15px; margin-top: 3px; }
  .holder__rule { flex: 1; height: 1.5px; background: var(--ink); margin-top: 6px; }

  .contacts { position: absolute; left: 33px; top: 276px; list-style: none; font-family: "Open Sans", sans-serif; font-size: 15px; color: var(--ink); }
  .contacts li { display: flex; align-items: center; gap: 8px; height: 23px; }
  .contacts svg { width: 14px; height: 12px; fill: var(--gold); flex: none; }

  .address { position: absolute; right: 32px; top: 297px; text-align: right; font-family: "Open Sans", sans-serif; font-size: 15px; line-height: 23px; color: var(--ink); font-style: normal; }

  .footer-band { position: absolute; left: 0; bottom: 0; width: 100%; height: 32px; background: var(--card-black); }
  .footer-band__gold { position: absolute; left: 0; top: 0; width: 305px; height: 100%; background: linear-gradient(90deg, var(--gold-deep), var(--gold-bright) 55%, var(--gold)); }
  .footer-band__dot { position: absolute; left: 312px; top: 7px; width: 18px; height: 18px; border-radius: 50%; background: var(--card-white); }
</style>
</head>
<body>
<main class="canvas">
  <section class="card card--front" aria-label="Business card front">
    <div class="brand">
      <span class="brand__mark"></span>
      <div class="brand__text">
        <span class="brand__name">Harbour Lane Dental</span>
        <span class="brand__tagline">Gentle care for every single smile</span>
      </div>
    </div>

    <div class="holder">
      <p class="holder__name">Marcus Hale, PHA</p>
      <p class="holder__role">President <span class="holder__rule"></span></p>
    </div>

    <ul class="contacts">
      <li>
        <svg viewBox="0 0 14 12" aria-hidden="true"><path d="M1 3c0-2 12-2 12 0v1.5h-3V3H4v1.5H1z"/><path d="M3 5h8l2 6H1z"/></svg>
        + 000 000 0000
      </li>
      <li>
        <svg viewBox="0 0 14 12" aria-hidden="true"><rect x="3.5" y="0" width="7" height="3.5"/><rect x="0" y="4" width="14" height="5" rx="1"/><rect x="3.5" y="8" width="7" height="4"/></svg>
        + 000 000 0000
      </li>
      <li>
        <svg viewBox="0 0 14 12" aria-hidden="true"><path d="M0 1h14v1L7 7 0 2z"/><path d="M0 3.5l7 5 7-5V11H0z"/></svg>
        info@harbourlanedental.com
      </li>
    </ul>

    <address class="address">Level 12, 48 Ridgeway House<br>Parramatta, New South Wales</address>

    <div class="footer-band">
      <span class="footer-band__gold"></span>
      <span class="footer-band__dot"></span>
    </div>
  </section>

  <section class="card card--back" aria-label="Business card back">
    <div class="brand">
      <span class="brand__mark"></span>
      <div class="brand__text">
        <span class="brand__name">Harbour Lane Dental</span>
        <span class="brand__tagline">Gentle care for every single smile</span>
      </div>
    </div>
  </section>
</main>
</body>
</html>
```